American cannabis tech company business card design

Pavrel.com is seeking a modern, professional, and brand-aligned business card that represents our company and its core values: Mission, Story, Values, and Impact. As an innovative cannabis company, we want a business card that is not only visually appealing but also serves as a representation of who we are and what we stand for.

Project Scope: Design a double-sided business card that integrates our brand identity and core values. Incorporate our key brand elements, ensuring a sleek and contemporary aesthetic. Visually reflect our core values (Mission, Story, Values, Impact) in a way that is engaging yet professional.

Target Market(s)

Vendors, third parties,

Contact Information for Business Card

Contact details (name, title, email, phone, website, etc.)

Font styles to use
Other font styles liked:
• Caslon, Centra

Colors

Designer to choose colors to be used in the design.

Requirements
Must have
• Pavrel.com logo and branding A creative yet clean way to integrate our core values (Mission, Story, Values, Impact) Modern typography and a well-structured layout
Nice to have
• forest green, grey, white, black
Should not have
• references to marijuana, leafs, plants, or related product

```html
<!DOCTYPE html>
<html lang="en">
<head>
<meta charset="utf-8">
<title>Pavrel.com Business Card</title>
<link rel="stylesheet" href="https://fonts.googleapis.com/css2?family=Libre+Caslon+Text:wght@400;700&family=Montserrat:wght@400;500&display=swap">
<style>
  :root {
    --backdrop: #1d1d1d;
    --forest: #1b3320;
    --forest-soft: #263a28;
    --paper: #ffffff;
    --cream: #f8f6ee;
    --ink-light: #f2f2ee;
    --font-serif: "Libre Caslon Text", "Times New Roman", serif;
    --font-sans: "Montserrat", Arial, sans-serif;
  }
  * { box-sizing: border-box; margin: 0; padding: 0; }
  html, body {
    width: 1200px;
    height: 1015px;
    overflow: hidden;
    background: var(--backdrop);
  }
  .sheet {
    width: 1200px;
    height: 1015px;
    display: flex;
    flex-direction: column;
    align-items: center;
    justify-content: center;
    gap: 60px;
  }
  .card {
    width: 620px;
    height: 354px;
    position: relative;
    overflow: hidden;
  }
  .card--front {
    background: var(--forest);
    display: flex;
    align-items: center;
    justify-content: center;
  }
  .wordmark {
    font-family: var(--font-serif);
    font-weight: 700;
    letter-spacing: 2px;
    line-height: 1;
  }
  .card--front .wordmark {
    color: var(--cream);
    font-size: 104px;
  }
  .card--back {
    display: flex;
  }
  .back-info {
    width: 50%;
    background: var(--forest-soft);
    color: var(--ink-light);
    padding: 46px 0 0 44px;
    position: relative;
  }
  .back-brand {
    width: 50%;
    background: var(--paper);
    display: flex;
    align-items: center;
    justify-content: center;
  }
  .back-brand .wordmark {
    color: var(--forest);
    font-size: 54px;
  }
  .holder-name {
    font-family: var(--font-serif);
    font-weight: 700;
    font-size: 19px;
  }
  .holder-title {
    font-family: var(--font-serif);
    font-size: 10px;
    margin-top: 4px;
    padding-left: 14px;
  }
  .address {
    position: absolute;
    left: 96px;
    top: 186px;
    font-family: var(--font-sans);
    font-size: 12px;
    line-height: 1.3;
  }
  .contact-list {
    position: absolute;
    left: 96px;
    top: 238px;
    list-style: none;
    font-family: var(--font-sans);
    font-size: 12px;
  }
  .contact-list li {
    display: flex;
    align-items: center;
    gap: 8px;
    margin-bottom: 8px;
  }
  .contact-list svg {
    width: 12px;
    height: 12px;
    fill: var(--ink-light);
    flex: none;
  }
</style>
</head>
<body>
<main class="sheet">
  <section class="card card--front" aria-label="Business card front">
    <span class="wordmark">PAVREL</span>
  </section>

  <section class="card card--back" aria-label="Business card back">
    <div class="back-info">
      <p class="holder-name">Daniel Harper</p>
      <p class="holder-title">Owner</p>
      <p class="address">418 Linden Ave, Suite 12<br>Dayton, OH 45402</p>
      <ul class="contact-list">
        <li>
          <svg viewBox="0 0 24 24" aria-hidden="true"><path d="M6.6 10.8a15.1 15.1 0 0 0 6.6 6.6l2.2-2.2c.3-.3.7-.4 1-.2 1.1.4 2.3.6 3.6.6.6 0 1 .4 1 1V20c0 .6-.4 1-1 1A17 17 0 0 1 3 4c0-.6.4-1 1-1h3.5c.6 0 1 .4 1 1 0 1.3.2 2.5.6 3.6.1.3 0 .7-.2 1z"/></svg>
          614-555-0192
        </li>
        <li>
          <svg viewBox="0 0 24 24" aria-hidden="true"><path d="M2 5h20v14H2z M2 5l10 8 10-8" fill="none" stroke="#f2f2ee" stroke-width="2"/><path d="M2 5h20l-10 8z"/></svg>
          info@pavrel.com
        </li>
        <li>
          <svg viewBox="0 0 24 24" aria-hidden="true"><circle cx="12" cy="12" r="10"/></svg>
          www.pavrel.com
        </li>
      </ul>
    </div>
    <div class="back-brand">
      <span class="wordmark">PAVREL</span>
    </div>
  </section>
</main>
</body>
</html>
```